Copperbend Blazeworks Website Design

I am looking for a website design ( Home page and inner template page ) in a .psd format. The home page needs to have a large hero image what will function as a "slider", and have some highlight graphical areas/links to the following links "Public & Municipal Events", "Corporate Events", "Special Events". The main navigation needs to have the following nav links "gallery", "home", "about", "services" and "contact". Unfortunately the client does not have any nice hi-rez images ( this is a company that specializes is large fireworks displays ) so please use stock photography sample images from snapvaultpics since we have an account there an can purchase the photos if our client wants to use them. Our current full time graphic artist has been with us for a long time so we are looking at artflockhub as a way to add a fresh approach to design and possibly find someone we can work with regularly. Here is a few designs that in the way we display them for our clients for approval. As you can see there are a couple that don't have their own images so they are utilizing the before mentioned snapvaultpics samples. On the plus side we did manage to get their logo in a .ai format. We have our team for handling the conversion from design to html.

http://reedfoxbuildstudio.com/dev/

```html
<!DOCTYPE html>
<html lang="en">
<head>
<meta charset="utf-8">
<title>Copperbend Blazeworks</title>
<link rel="stylesheet" href="https://fonts.googleapis.com/css2?family=Lato:wght@300;400;700;900&family=Montserrat:wght@500;600&family=Poppins:wght@300&display=swap">
<style>
:root{
  --blue:#3a8fd6;
  --blue-deep:#4455e0;
  --grey-text:#7d7d82;
  --heading-grey:#8a8a8f;
  --white:#ffffff;
  --line:#9a9a9a;
}
*{margin:0;padding:0;box-sizing:border-box}
html,body{width:725px;height:1200px;overflow:hidden;background:var(--white)}
body{position:relative;font-family:'Lato',sans-serif;color:var(--grey-text)}

/* header */
.site-header{position:absolute;left:0;top:0;width:725px;height:69px;background:var(--white);z-index:2}
.brand{position:absolute;left:87px;top:27px;font-weight:400;font-size:13px;color:#3a3a44;display:flex;align-items:center;gap:5px}
.brand-dot{width:10px;height:10px;border-radius:50%;background:var(--blue);flex:none}
.call{position:absolute;left:471px;top:13px;display:flex;align-items:center;gap:4px}
.call-icon{width:18px;height:18px;border-radius:50%;background:var(--blue);display:flex;align-items:center;justify-content:center}
.call-text{font-size:7px;line-height:8px;color:#333}
.call-text b{display:block;color:var(--blue);font-weight:700;font-size:8px}
.header-rule{position:absolute;left:564px;top:13px;width:1px;height:18px;background:#ccc}
.socials{position:absolute;left:570px;top:15px;display:flex;gap:4px}
.socials span{width:14px;height:14px;border-radius:50%;border:1.2px solid var(--blue)}
.nav{position:absolute;left:381px;top:39px;height:18px;display:flex;align-items:center;font-size:9px;color:#333}
.nav a{text-decoration:none;color:#333;margin-right:25px}
.nav a.active{background:var(--blue);color:#fff;padding:0 13px;height:18px;line-height:18px;margin-right:10px;transform:skewX(-12deg)}
.nav a.active span{display:inline-block;transform:skewX(12deg)}
.nav a:last-child{margin-right:0}

/* hero */
.hero{position:absolute;left:0;top:69px;width:725px;height:295px;background:radial-gradient(ellipse at 30% 30%,#4a2a22 0%,#241622 40%,#120f1a 80%),#120f1a}
.hero-glow{position:absolute;left:360px;top:70px;width:360px;height:225px;background:radial-gradient(ellipse at 55% 45%,rgba(150,110,70,.55),rgba(40,30,50,0) 70%)}
.hero-title{position:absolute;left:87px;top:158px;color:#fff;z-index:2}
.hero-title .light{font-weight:300;font-size:26px;letter-spacing:.5px;line-height:30px}
.hero-title .bold{font-weight:900;font-size:33px;line-height:38px;letter-spacing:-.5px}

/* event cards */
.event-card{position:absolute;top:311px;width:178px;height:91px;background:#fff;box-shadow:0 2px 6px rgba(0,0,0,.08);padding:17px 19px 0;z-index:3}
.event-card.grey{border-top:6px solid #8e8e93;padding-top:11px}
.event-card.featured{background:linear-gradient(120deg,var(--blue),var(--blue-deep))}
.event-card h3{font-size:11px;font-weight:400;color:#333;margin-bottom:8px}
.event-card p{font-size:7.3px;line-height:11.7px;color:#555}
.event-card.featured h3,.event-card.featured p{color:#fff}
.event-card .arrow{position:absolute;right:20px;bottom:10px}

/* welcome */
.welcome-bg{position:absolute;left:0;top:364px;width:725px;height:308px;background:linear-gradient(180deg,#fff,#f7f9fc)}
.eyebrow{position:absolute;font-size:11px;color:var(--heading-grey)}
.section-heading{position:absolute;font-size:24px;font-weight:700;color:var(--heading-grey);letter-spacing:-.2px;white-space:nowrap}
.section-heading em{font-style:normal;color:var(--blue)}
.rule{position:absolute;height:2px;background:var(--line)}
.body-copy{position:absolute;font-size:8.4px;line-height:13.6px;font-weight:300;color:var(--grey-text)}
.btn{position:absolute;height:23px;background:linear-gradient(90deg,var(--blue),var(--blue-deep));color:#fff;font-size:7.6px;font-weight:700;display:flex;align-items:center;justify-content:center;border-radius:2px}
.video-frame{position:absolute;left:371px;top:438px;width:317px;height:173px;background:#c8c8c8}
.side-photo{position:absolute;top:468px;height:122px}
.video{position:absolute;left:418px;top:443px;width:263px;height:173px;background:radial-gradient(ellipse at 30% 65%,#2a6a4a 0%,rgba(0,0,0,0) 35%),radial-gradient(ellipse at 65% 45%,#7a3a6a 0%,rgba(0,0,0,0) 40%),radial-gradient(ellipse at 80% 70%,#8a6a50 0%,rgba(0,0,0,0) 35%),#050709}
.play{position:absolute;left:534px;top:512px;width:34px;height:34px;border-radius:50%;background:#fff;box-shadow:0 0 0 2px rgba(255,255,255,.35)}

/* testimonials */
.clients{position:absolute;left:0;top:672px;width:725px;height:314px;background:radial-gradient(ellipse at 40% 60%,#f6e6f0 0%,#ece9f2 55%,#e7e6ec 100%)}
.quote-card{position:absolute;text-align:center;background:#fafafc;box-shadow:0 3px 8px rgba(0,0,0,.08);overflow:hidden}
.quote-card .mark{font-weight:900;font-size:34px;line-height:30px;color:#d5d5da}
.quote-card p{font-size:5.8px;line-height:9.4px;color:#a0a0a6}
.quote-card .name{font-family:'Montserrat',sans-serif;font-weight:500;font-size:7px;color:#9a9aa0;margin-top:23px;white-space:nowrap}
.quote-card .place{font-size:5px;color:#a0a0a6;margin-top:3px}
.quote-card.main{background:linear-gradient(135deg,var(--blue-deep),var(--blue));box-shadow:0 4px 12px rgba(40,60,160,.25);z-index:2}
.quote-card.main .mark{color:#8fb4f2;font-size:44px;line-height:38px}
.quote-card.main p{font-size:7.2px;line-height:11.8px;color:#fff}
.quote-card.main .divider{width:37px;height:1px;background:rgba(255,255,255,.35);margin:17px auto 0}
.quote-card.main .name{color:#fff;font-weight:600;font-size:8.6px;margin-top:12px}
.quote-card.main .place{color:#fff;font-size:6.3px;margin-top:4px}
.dots{position:absolute;left:229px;top:914px;display:flex;gap:3px;align-items:center}
.dots span{width:5px;height:5px;border-radius:50%;background:#b9b9c2}
.dots span.on{width:8px;height:8px;background:var(--blue)}

/* footer */
.footer{position:absolute;left:0;top:986px;width:725px;height:214px;background:radial-gradient(ellipse at 60% 80%,#4a1f4a 0%,#1e1b33 50%,#12121f 100%)}
.newsletter{position:absolute;left:87px;top:948px;width:551px;height:78px;background:linear-gradient(100deg,var(--blue) 40%,var(--blue-deep));box-shadow:0 3px 10px rgba(0,0,0,.2);z-index:3}
.newsletter h2{position:absolute;left:44px;top:26px;font-family:'Poppins',sans-serif;font-weight:300;font-size:18px;color:#fff}
.newsletter .email{position:absolute;left:249px;top:28px;width:171px;height:23px;background:#fff;border:1px solid #ccc;font-size:9px;color:#777;padding:6px 9px}
.newsletter .signup{position:absolute;left:426px;top:28px;width:80px;height:23px;background:var(--blue-deep);border:1px solid #6d8be8;color:#fff;font-weight:700;font-size:11px;display:flex;align-items:center;justify-content:center}
.foot-brand{position:absolute;left:87px;top:1092px;width:105px;font-size:13px;line-height:15px;font-weight:400;color:#fff;display:flex;align-items:center;gap:5px}
.foot-socials{position:absolute;left:100px;top:1133px;display:flex;gap:2px}
.foot-socials span{width:18px;height:18px;border-radius:50%;border:1.3px solid #fff}
.office{position:absolute;top:1051px;color:#fff;font-size:7.3px;line-height:11px}
.office h4{font-size:9.4px;font-weight:700;margin-bottom:5px}
.office .gap{height:7px}
.foot-divider{position:absolute;left:331px;top:1050px;width:1px;height:118px;background:rgba(255,255,255,.25)}
.map{position:absolute;left:476px;top:1050px;width:162px;height:118px;background:linear-gradient(135deg,#efe6cf,#e8dcc0)}
.foot-rule{position:absolute;left:87px;top:1168px;width:551px;height:1px;background:rgba(255,255,255,.25)}
.copyright{position:absolute;left:0;top:1181px;width:725px;text-align:center;font-size:8px;color:#fff}
</style>
</head>
<body>

<header class="site-header">
  <div class="brand"><span class="brand-dot"></span>Copperbend Blazeworks</div>
  <div class="call">
    <div class="call-icon">
      <svg width="9" height="9" viewBox="0 0 24 24"><path d="M6.6 10.8a15 15 0 0 0 6.6 6.6l2.2-2.2a1 1 0 0 1 1-.25 11.4 11.4 0 0 0 3.6.57 1 1 0 0 1 1 1V20a1 1 0 0 1-1 1A17 17 0 0 1 3 4a1 1 0 0 1 1-1h3.5a1 1 0 0 1 1 1c0 1.25.2 2.45.57 3.57a1 1 0 0 1-.25 1z" fill="#fff"/></svg>
    </div>
    <div class="call-text">Call US<b>+1-555-014-2290</b></div>
  </div>
  <div class="header-rule"></div>
  <div class="socials"><span></span><span></span><span></span><span></span></div>
  <nav class="nav">
    <a class="active" href="#"><span>Home</span></a>
    <a href="#">About</a>
    <a href="#">Services</a>
    <a href="#">Gallery</a>
    <a href="#">Contact</a>
  </nav>
</header>

<section class="hero" role="img" aria-label="Two people in winter hats watching a fireworks display at night">
  <div class="hero-glow"></div>
</section>
<div class="hero-title">
  <div class="light">WELCOME</div>
  <div class="bold">TO OUR SITE!</div>
</div>

<section class="welcome-bg"></section>

<article class="event-card featured" style="left:87px">
  <h3>Public &amp; Municipal Events</h3>
  <p>Lorem Ipsum has been the<br>standard dummy text ever since the</p>
  <svg class="arrow" width="14" height="6" viewBox="0 0 14 6"><path d="M0 3h13M10 .5 13 3l-3 2.5" stroke="#fff" stroke-width=".8" fill="none"/></svg>
</article>
<article class="event-card grey" style="left:274px">
  <h3>Corporate Events</h3>
  <p>Lorem Ipsum has been the<br>standard dummy text ever since the</p>
  <svg class="arrow" width="14" height="6" viewBox="0 0 14 6"><path d="M0 3h13M10 .5 13 3l-3 2.5" stroke="#555" stroke-width=".8" fill="none"/></svg>
</article>
<article class="event-card grey" style="left:460px">
  <h3>Special Events</h3>
  <p>Lorem Ipsum has been the<br>standard dummy text ever since the</p>
  <svg class="arrow" width="14" height="6" viewBox="0 0 14 6"><path d="M0 3h13M10 .5 13 3l-3 2.5" stroke="#555" stroke-width=".8" fill="none"/></svg>
</article>

<div class="eyebrow" style="left:87px;top:449px">Welcome to</div>
<h1 class="section-heading" style="left:87px;top:462px"><em>Copperbend</em> Blazeworks</h1>
<div class="rule" style="left:87px;top:498px;width:85px"></div>
<p class="body-copy" style="left:87px;top:513px;width:262px">Lorem Ipsum is simply dummy text of the printing and typesetting industry. Lorem Ipsum has been the industry's standard dummy text ever since the 1500s, when an unknown printer took a galley of type and scrambled it to make a type specimen book. It has survived not only five centuries, but also the leap into electronic typesetting, remaining essentially unchanged.</p>
<div class="btn" style="left:87px;top:606px;width:77px">LEARN MORE</div>

<div class="video-frame"></div>
<div class="side-photo" style="left:375px;width:43px;background:linear-gradient(135deg,#6a3a1c,#2a160e)" role="img" aria-label="Crowd silhouettes against an orange glow"></div>
<div class="side-photo" style="left:681px;width:44px;background:linear-gradient(135deg,#3a2418,#7a4a2a)" role="img" aria-label="Hand holding a sparkler"></div>
<div class="video" role="img" aria-label="Video still of colourful fireworks bursting in a night sky"></div>
<div class="play">
  <svg width="34" height="34" viewBox="0 0 34 34"><path d="M14 11.5v11l9-5.5z" fill="#5a4a6a"/></svg>
</div>

<section class="clients"></section>
<div class="quote-card" style="left:87px;top:727px;width:85px;height:157px;padding:20px 5px 0 9px;text-align:left">
  <div class="mark" style="padding-left:47px">&ldquo;</div>
  <p style="margin-top:8px">Lorem Ipsum is simply dummy text of the printing and typesetting industry. Lorem Ipsum has been the industry's standard dummy text ever since the 1500s,</p>
  <div class="name" style="padding-left:23px">Daniel R</div>
  <div class="place" style="padding-left:44px">ASHMERE</div>
</div>
<div class="quote-card" style="left:308px;top:727px;width:89px;height:157px;padding:20px 6px 0 4px">
  <div class="mark">&ldquo;</div>
  <p style="margin-top:8px">ipsum is simply dummy text printing and typesetting Lorem Ipsum has been the y's standard dummy text ever since the 1500s,</p>
  <div class="name">Daniel R Fenwick</div>
  <div class="place">ASHMERE</div>
</div>
<div class="quote-card main" style="left:167px;top:709px;width:145px;height:192px;padding:24px 11px 0">
  <div class="mark">&ldquo;</div>
  <p style="margin-top:12px">Lorem Ipsum is simply dummy text of the printing and typesetting industry. Lorem Ipsum has been the industry's standard dummy text ever since the 1500s,</p>
  <div class="divider"></div>
  <div class="name">Daniel R Fenwick</div>
  <div class="place">ASHMERE</div>
</div>
<div class="dots"><span></span><span class="on"></span><span></span></div>

<div class="eyebrow" style="left:425px;top:725px">Our</div>
<h2 class="section-heading" style="left:425px;top:737px"><em>Happy</em> Client’s</h2>
<div class="rule" style="left:425px;top:774px;width:77px"></div>
<p class="body-copy" style="left:425px;top:788px;width:214px">Lorem Ipsum is simply dummy text of the printing and typesetting industry. Lorem Ipsum has been the industry's standard dummy text ever since the 1500s, when an unknown printer took a galley of type and scrambled it to make a type specimen book.</p>
<div class="btn" style="left:425px;top:881px;width:77px">LEARN MORE</div>

<footer class="footer"></footer>
<div class="newsletter">
  <h2>Sign up for newsletter</h2>
  <div class="email">Your Email</div>
  <div class="signup">SIGN UP</div>
</div>

<div class="foot-brand"><span class="brand-dot"></span><span>Copperbend<br>Blazeworks</span></div>
<div class="foot-socials"><span></span><span></span><span></span><span></span></div>

<div class="office" style="left:211px">
  <h4>Corporate Headquarters</h4>
  4410 Marrow Lane,<br>ASHMERE, WI,<br>Wisconsin, 54011.
  <div class="gap"></div>
  Phone: 555-014-3380
  <div class="gap" style="height:5px"></div>
  Email: info@copperbend.example
</div>
<div class="foot-divider"></div>
<div class="office" style="left:350px">
  <h4>Southeast Regional Office</h4>
  4410 Marrow Lane,<br>ASHMERE, WI,<br>Wisconsin, 54011.
  <div class="gap"></div>
  Phone: 555-014-3380
  <div class="gap" style="height:5px"></div>
  Email: info@copperbend.example
</div>
<div class="map" role="img" aria-label="Road map showing the office locations"></div>
<div class="foot-rule"></div>
<div class="copyright">Copperbend Blazeworks © 2021 All Rights Reserved | Privacy Policy | Terms and Conditions</div>

</body>
</html>
```